Website Quibrel Outdoor

Hi I'm looking for a simple design for a new website. It's outdoor products mainly in category, Boat, Tarpaulin, Fishing, Golf. I have include image and text for 8 products + presentation etc. I want a simple and modern site + fast + Mobile. Wordpress. I'm going to sell through Tradovik so I don't need any WooCommerce but a buy button to Tradovik. I haven set up the Tradovik account yet. My logo i s grey and orange. My goal is to sell in Tradovik US and later EU.

```html
<!DOCTYPE html>
<html lang="en">
<head>
<meta charset="utf-8">
<title>Quibrel Outdoor</title>
<link href="https://fonts.googleapis.com/css2?family=Montserrat:wght@500;600;700&family=Lato:wght@400;700&display=swap" rel="stylesheet">
<style>
:root{
  --orange:#f0821e;
  --orange-light:#f6a24e;
  --dark:#232323;
  --footer:#1c1c1c;
  --ink:#1e1e1e;
  --text:#4a4a4a;
  --white:#ffffff;
  --star:#f1a11f;
}
*{margin:0;padding:0;box-sizing:border-box}
html,body{width:1200px;height:3963px;overflow:hidden}
body{position:relative;font-family:"Lato",sans-serif;color:var(--text);background:var(--white)}
.abs{position:absolute}
h1,h2,h3,.brand,.btn{font-family:"Montserrat",sans-serif}
.btn{display:inline-flex;align-items:center;justify-content:center;gap:8px;background:var(--orange);color:var(--white);font-weight:600;border-radius:30px;text-decoration:none}

/* hero */
.hero{left:0;top:0;width:1200px;height:615px;background:linear-gradient(100deg,#2a3122 0%,#3c4530 40%,#5a4a32 65%,#2c2e26 100%)}
.hero-person{left:640px;top:70px;width:430px;height:545px;border-radius:40% 40% 0 0;background:linear-gradient(180deg,#7a4a2a 0%,#c85a1e 40%,#3a3a3e 100%);opacity:.55}
.site-logo{left:111px;top:44px;width:150px;color:var(--orange);font-size:26px;font-weight:700;line-height:1.05}
.site-logo.light span{color:var(--orange)}
.nav{left:441px;top:48px;display:flex;gap:44px;font-size:14.5px;color:var(--white)}
.nav .active{color:var(--orange)}
.nav-icons{left:1012px;top:46px;display:flex;gap:12px}
.hero h1{left:111px;top:232px;font-size:44px;font-weight:700;color:var(--white)}
.hero-text{left:111px;top:302px;width:540px;font-size:15px;line-height:24px;color:var(--white)}
.hero .btn{left:111px;top:375px;width:161px;height:57px;font-size:15px}

/* about */
.about-logo{left:111px;top:700px;width:480px;height:420px;display:flex;align-items:center;justify-content:center;gap:18px}
.about-logo .dot{width:70px;height:70px;border-radius:50%;background:#6b6b6b}
.about-logo .brand{font-size:48px;font-weight:700;color:var(--orange);line-height:1.1}
.eyebrow{left:649px;top:724px;font-size:14px;font-weight:700;color:var(--orange)}
.about h2{left:649px;top:745px;font-size:38px;font-weight:700;color:var(--ink)}
.about-text{left:649px;top:805px;width:450px;font-size:14.5px;line-height:30px;color:var(--text)}
.about .btn{left:649px;top:1040px;width:155px;height:48px;font-size:14px}

/* products */
.products{left:0;top:1200px;width:1200px;height:600px;background:linear-gradient(180deg,#ee8420 0%,#e97d1a 100%)}
.products h2,.reviews h2{width:1200px;text-align:center;font-size:34px;font-weight:700;color:var(--white)}
.products h2{top:68px}
.card{top:136px;width:233px;height:369px;background:var(--white);border-radius:6px;text-align:center;box-shadow:0 2px 8px rgba(0,0,0,.12)}
.card .thumb{margin:16px auto 0;width:140px;height:130px;border-radius:8px}
.card h3{margin-top:22px;font-size:18px;font-weight:600;color:var(--ink);line-height:30px;padding:0 20px}
.stars{margin-top:10px;display:flex;justify-content:center;gap:4px}
.price{margin-top:10px;font-size:14px;color:var(--text)}
.price s{margin-right:6px}
.price b{color:var(--orange);font-weight:400}
.cart{margin:12px auto 0;width:146px;height:37px;border:2px solid var(--orange);border-radius:20px;color:var(--orange);font-size:13.5px;display:flex;align-items:center;justify-content:center;gap:6px}

/* services */
.section-title{width:1200px;text-align:center;font-size:34px;font-weight:700;color:var(--ink)}
.rule{left:569px;width:62px;height:3px;background:var(--orange)}
.service{top:1969px;width:222px;text-align:center}
.service .ring{width:222px;height:222px;border-radius:50%;border:9px solid var(--orange-light)}
.service h3{margin-top:22px;font-size:26px;font-weight:700;color:var(--ink)}

/* reviews */
.reviews{left:0;top:2330px;width:1200px;height:470px;background:linear-gradient(180deg,#ef8420,#e87b18)}
.reviews h2{top:62px}
.quote-text{left:240px;top:200px;width:720px;text-align:center;font-size:15px;line-height:24px;color:var(--white)}
.avatar{border-radius:50%;border:3px solid var(--orange-light);background:linear-gradient(135deg,#c89a7a,#6b4a3a)}
.reviewer{top:2384px;width:1200px;text-align:center}
.reviewer-name{left:0;top:378px;width:1215px;text-align:center;font-size:15px;font-weight:700;color:var(--white)}

/* news */
.news-intro{left:240px;top:2935px;width:720px;text-align:center;font-size:14.5px;line-height:30px;color:var(--text)}
.tile{width:245px;height:256px}
.post{padding:36px 18px;color:var(--white)}
.post.orange{background:var(--orange)}
.post.dark{background:var(--dark)}
.post .date{font-size:15px}
.post h3{margin-top:6px;font-size:24px;font-weight:700}
.post p{margin-top:12px;font-size:14.5px;line-height:30px}
.post .more{margin-top:8px;font-family:"Montserrat",sans-serif;font-weight:600;font-size:15px;display:flex;align-items:center;gap:12px}

/* footer */
.footer{left:0;top:3622px;width:1200px;height:341px;background:var(--footer);color:var(--white)}
.footer-logo{left:140px;top:62px;font-size:26px;font-weight:700;color:var(--orange);width:160px;text-align:center;line-height:1.1}
.social{top:180px;display:flex;gap:11px;left:111px}
.social span{width:39px;height:39px;border-radius:50%;border:1.5px solid var(--white)}
.social span:first-child{background:var(--orange);border-color:var(--orange)}
.footer-nav{left:374px;top:68px;width:420px;display:flex;flex-wrap:wrap;column-gap:48px;row-gap:16px;font-family:"Montserrat",sans-serif;font-weight:600;font-size:14px}
.footer-nav .active{color:var(--orange)}
.footer-text{left:374px;top:144px;width:380px;font-size:14.5px;line-height:30px}
.subscribe{left:846px;top:66px;font-family:"Montserrat",sans-serif;font-weight:700;font-size:18.5px}
.email{left:846px;top:104px;width:230px;height:38px;border:1px solid #3a3a3a;background:#111;font-size:14.5px;padding:10px 13px;color:#ddd}
.email-send{left:1032px;top:108px;width:46px;height:31px;background:var(--orange);display:flex;align-items:center;justify-content:center}
.divider{left:0;top:248px;width:1200px;height:1px;background:#2e2e2e}
.copyright{left:0;top:278px;width:1200px;text-align:center;font-size:14.5px}
</style>
</head>
<body>

<!-- Hero -->
<section class="hero abs">
  <div class="hero-person abs" role="img" aria-label="Photo of a woman in an orange jacket fishing by a forest stream"></div>
  <div class="site-logo abs brand">Quibrel Outdoor</div>
  <nav class="nav abs"><span class="active">Home</span><span>About Us</span><span>Category</span><span>Products</span><span>Contact Us</span></nav>
  <div class="nav-icons abs">
    <svg width="16" height="16" viewBox="0 0 16 16"><circle cx="6.5" cy="6.5" r="4.5" fill="none" stroke="#fff" stroke-width="2"/><path d="M10 10l4 4" stroke="#fff" stroke-width="2.2"/></svg>
    <svg width="16" height="16" viewBox="0 0 16 16"><path d="M5 5V4a3 3 0 016 0v1" fill="none" stroke="#fff" stroke-width="1.6"/><rect x="2.5" y="5" width="11" height="10" rx="1.5" fill="#fff"/></svg>
    <svg width="17" height="16" viewBox="0 0 17 16"><path d="M8.5 14L2.5 8a3.4 3.4 0 016-4 3.4 3.4 0 016 4z" fill="none" stroke="#fff" stroke-width="1.6"/></svg>
  </div>
  <h1 class="abs">Welcome To Quibrel Outdoor</h1>
  <p class="hero-text abs">Lorem ipsum dolor sit amet, consectetur adipiscing elit, sed do eiusmod tempor incididunt ut labore et dolore magna aliqua.</p>
  <a class="btn abs">Learn More</a>
</section>

<!-- About -->
<section class="about">
  <div class="about-logo abs"><span class="dot"></span><span class="brand">Quibrel<br>Outdoor</span></div>
  <div class="eyebrow abs">About Us</div>
  <h2 class="abs">Quibrel Outdoor</h2>
  <p class="about-text abs">Lorem ipsum dolor sit amet, consectetur adipiscing elit, sed do eiusmod tempor incididunt ut labore et dolore magna aliqua. Quis ipsum suspendisse ultrices gravida. Risus commodo viverra maecenas accumsan lacus vel facilisis. Lorem ipsum dolor sit amet, consectetur adipiscing elit, sed do eiusmod tempor incididunt ut labore et dolore magna aliqua. Quis ipsum suspendisse ultrices gravida. Risus commodo</p>
  <a class="btn abs">Learn More
    <svg width="14" height="14" viewBox="0 0 14 14"><circle cx="7" cy="7" r="7" fill="#fff"/><path d="M4 7h5M7 4.5L9.5 7 7 9.5" stroke="#f0821e" stroke-width="1.8" fill="none"/></svg>
  </a>
</section>

<!-- Products -->
<section class="products abs">
  <h2 class="abs">Our Products</h2>
  <div class="card abs" style="left:111px">
    <div class="thumb" role="img" aria-label="Clear water weight bag" style="background:linear-gradient(135deg,#e8e8e8,#bdbdbd)"></div>
    <h3>Trapaulin Weight Bag</h3>
    <div class="stars"><svg width="96" height="16" viewBox="0 0 96 16"><g fill="#f1a11f"><path id="st" d="M8 0l2.4 5 5.4.6-4 3.7 1.1 5.4L8 12l-4.9 2.7 1.1-5.4-4-3.7 5.4-.6z"/><use href="#st" x="20"/><use href="#st" x="40"/><use href="#st" x="60"/><use href="#st" x="80"/></g></svg></div>
    <p class="price"><s>$49.00</s><b>$ 19.97</b></p>
    <div class="cart"><svg width="12" height="12" viewBox="0 0 12 12"><path d="M1 1h2l1.5 6h6l1-4H4" fill="none" stroke="#f0821e" stroke-width="1.2"/><circle cx="5" cy="10" r="1" fill="#f0821e"/><circle cx="9.5" cy="10" r="1" fill="#f0821e"/></svg>Add to Cart</div>
  </div>
  <div class="card abs" style="left:359px">
    <div class="thumb" role="img" aria-label="Magnifier glasses on a black cord" style="background:linear-gradient(135deg,#f2f2f6,#c7c8d8)"></div>
    <h3>Magnififier Glasses</h3>
    <div class="stars"><svg width="96" height="16" viewBox="0 0 96 16"><g fill="#f1a11f"><use href="#st"/><use href="#st" x="20"/><use href="#st" x="40"/><use href="#st" x="60"/><use href="#st" x="80"/></g></svg></div>
    <p class="price"><s>$49.00</s><b>$ 19.97</b></p>
    <div class="cart"><svg width="12" height="12" viewBox="0 0 12 12"><path d="M1 1h2l1.5 6h6l1-4H4" fill="none" stroke="#f0821e" stroke-width="1.2"/><circle cx="5" cy="10" r="1" fill="#f0821e"/><circle cx="9.5" cy="10" r="1" fill="#f0821e"/></svg>Add to Cart</div>
  </div>
  <div class="card abs" style="left:607px">
    <div class="thumb" role="img" aria-label="Grey towel with orange holder" style="background:linear-gradient(135deg,#9a9a9a,#5a5a5a)"></div>
    <h3>Towel with holder kopiera</h3>
    <div class="stars"><svg width="96" height="16" viewBox="0 0 96 16"><g fill="#f1a11f"><use href="#st"/><use href="#st" x="20"/><use href="#st" x="40"/><use href="#st" x="60"/><use href="#st" x="80"/></g></svg></div>
    <p class="price"><s>$49.00</s><b>$ 19.97</b></p>
    <div class="cart"><svg width="12" height="12" viewBox="0 0 12 12"><path d="M1 1h2l1.5 6h6l1-4H4" fill="none" stroke="#f0821e" stroke-width="1.2"/><circle cx="5" cy="10" r="1" fill="#f0821e"/><circle cx="9.5" cy="10" r="1" fill="#f0821e"/></svg>Add to Cart</div>
  </div>
  <div class="card abs" style="left:855px">
    <div class="thumb" role="img" aria-label="Emergency urinal bottle with blue funnel" style="background:linear-gradient(135deg,#dfe6f6,#3a5ee0)"></div>
    <h3>Emergency Bottle Urinoar</h3>
    <div class="stars"><svg width="96" height="16" viewBox="0 0 96 16"><g fill="#f1a11f"><use href="#st"/><use href="#st" x="20"/><use href="#st" x="40"/><use href="#st" x="60"/><use href="#st" x="80"/></g></svg></div>
    <p class="price"><s>$49.00</s><b>$ 19.97</b></p>
    <div class="cart"><svg width="12" height="12" viewBox="0 0 12 12"><path d="M1 1h2l1.5 6h6l1-4H4" fill="none" stroke="#f0821e" stroke-width="1.2"/><circle cx="5" cy="10" r="1" fill="#f0821e"/><circle cx="9.5" cy="10" r="1" fill="#f0821e"/></svg>Add to Cart</div>
  </div>
</section>

<!-- Services -->
<section class="services">
  <h2 class="section-title abs" style="top:1876px">Our Services</h2>
  <div class="rule abs" style="top:1929px"></div>
  <div class="service abs" style="left:111px"><div class="ring" role="img" aria-label="Photo of a woman stepping onto a boat" style="background:linear-gradient(135deg,#9aa4ae,#3e4650)"></div><h3>Boat</h3></div>
  <div class="service abs" style="left:362px"><div class="ring" role="img" aria-label="Photo of a tarpaulin frame on a boat" style="background:linear-gradient(135deg,#6a6a6a,#d8d2c8)"></div><h3>Presenning</h3></div>
  <div class="service abs" style="left:613px"><div class="ring" role="img" aria-label="Photo of a woman fishing outdoors" style="background:linear-gradient(135deg,#3e4a36,#c85a1e)"></div><h3>Outdoor</h3></div>
  <div class="service abs" style="left:864px"><div class="ring" role="img" aria-label="Photo of a blue net bag indoors" style="background:linear-gradient(135deg,#1f3f9a,#c9d6e8)"></div><h3>Indoor</h3></div>
</section>

<!-- Reviews -->
<section class="reviews abs">
  <h2 class="abs">Our Clients Reviews</h2>
  <svg class="abs" style="left:574px;top:138px" width="52" height="40" viewBox="0 0 52 40"><path d="M0 40V22C0 10 6 2 18 0l2 6C13 8 10 12 10 18h12v22zM30 40V22C30 10 36 2 48 0l2 6c-7 2-10 6-10 12h12v22z" fill="#fff"/></svg>
  <p class="quote-text abs">Lorem ipsum dolor sit amet, consectetur adipiscing elit, sed do eiusmod tempor incididunt ut labore et dolore magna aliqua. Quis ipsum suspendisse ultrices gravida. Risus commodo viverra maecenas accumsan lacus vel facilisis.</p>
  <svg class="abs" style="left:176px;top:228px" width="10" height="16" viewBox="0 0 10 16"><path d="M8 2L2 8l6 6" stroke="#fff" stroke-width="1.6" fill="none"/></svg>
  <svg class="abs" style="left:1015px;top:228px" width="10" height="16" viewBox="0 0 10 16"><path d="M2 2l6 6-6 6" stroke="#fff" stroke-width="1.6" fill="none"/></svg>
  <div class="avatar abs" role="img" aria-label="Client portrait" style="left:513px;top:328px;width:44px;height:44px"></div>
  <div class="avatar abs" role="img" aria-label="Client portrait" style="left:570px;top:322px;width:56px;height:56px"></div>
  <div class="avatar abs" role="img" aria-label="Client portrait" style="left:638px;top:328px;width:44px;height:44px"></div>
  <div class="reviewer-name abs">Maren Holloway</div>
</section>

<!-- News -->
<section class="news">
  <h2 class="section-title abs" style="top:2878px">Latest News</h2>
  <p class="news-intro abs">Lorem ipsum dolor sit amet, consectetur adipiscing elit, sed do eiusmod tempor incididunt ut labore et dolore magna aliqua. Quis ipsum suspendisse ultrices gravida.</p>

  <article class="tile post orange abs" style="left:111px;top:3018px">
    <div class="date">Dec 16 2021</div><h3>Lorem Ipsum</h3>
    <p>Lorem ipsum dolor sit amet, consectetur adipiscing elit, sed do eiusmod</p>
    <div class="more">Learn More <svg width="14" height="12" viewBox="0 0 14 12"><path d="M0 6h12M7 1l5 5-5 5" stroke="#fff" stroke-width="2" fill="none"/></svg></div>
  </article>
  <div class="tile abs" role="img" aria-label="Photo of a covered greenhouse with water weight bags" style="left:356px;top:3018px;background:linear-gradient(160deg,#8a9098,#3a3e44)"></div>
  <article class="tile post orange abs" style="left:600px;top:3018px">
    <div class="date">Dec 16 2021</div><h3>Lorem Ipsum</h3>
    <p>Lorem ipsum dolor sit amet, consectetur adipiscing elit, sed do eiusmod</p>
    <div class="more">Learn More <svg width="14" height="12" viewBox="0 0 14 12"><path d="M0 6h12M7 1l5 5-5 5" stroke="#fff" stroke-width="2" fill="none"/></svg></div>
  </article>
  <div class="tile abs" role="img" aria-label="Photo of a golf bag on a trolley on grass" style="left:844px;top:3018px;background:linear-gradient(160deg,#6f9a4a,#2e3a2a)"></div>

  <div class="tile abs" role="img" aria-label="Photo of a woman loading a towel into a washing machine" style="left:111px;top:3274px;background:linear-gradient(160deg,#d8d4cc,#4a6a8a)"></div>
  <article class="tile post dark abs" style="left:356px;top:3274px">
    <div class="date">Dec 16 2021</div><h3>Lorem Ipsum</h3>
    <p>Lorem ipsum dolor sit amet, consectetur adipiscing elit, sed do eiusmod</p>
    <div class="more">Learn More <svg width="14" height="12" viewBox="0 0 14 12"><path d="M0 6h12M7 1l5 5-5 5" stroke="#fff" stroke-width="2" fill="none"/></svg></div>
  </article>
  <div class="tile abs" role="img" aria-label="Photo of a man climbing a ladder onto a boat" style="left:600px;top:3274px;background:linear-gradient(160deg,#b0b4b8,#2a2c30)"></div>
  <article class="tile post dark abs" style="left:844px;top:3274px">
    <div class="date">Dec 16 2021</div><h3>Lorem Ipsum</h3>
    <p>Lorem ipsum dolor sit amet, consectetur adipiscing elit, sed do eiusmod</p>
    <div class="more">Learn More <svg width="14" height="12" viewBox="0 0 14 12"><path d="M0 6h12M7 1l5 5-5 5" stroke="#fff" stroke-width="2" fill="none"/></svg></div>
  </article>
</section>

<!-- Footer -->
<footer class="footer abs">
  <div class="footer-logo abs brand">Quibrel Outdoor</div>
  <div class="social abs"><span></span><span></span><span></span><span></span></div>
  <nav class="footer-nav abs"><span class="active">Home</span><span>About Us</span><span>Category</span><span>Products</span><span>Contact Us</span></nav>
  <p class="footer-text abs">Lorem ipsum dolor sit amet, consectetur adipiscing elit, sed do eiusmod tempor incididunt</p>
  <div class="subscribe abs">Subscribe Our Newslter</div>
  <div class="email abs">Your Email</div>
  <div class="email-send abs"><svg width="18" height="16" viewBox="0 0 18 16"><path d="M1 7L17 1l-4 14-4-5zM9 10l8-9" fill="none" stroke="#fff" stroke-width="1.4"/></svg></div>
  <div class="divider abs"></div>
  <p class="copyright abs">©Copyrights 2021&nbsp; Company Name&nbsp; |&nbsp;&nbsp; All Rights Reserved</p>
</footer>

</body>
</html>
```